Oral Surgeon Referral Pads

Hello. We need referral pads for Dr Elsabet Quorvane, DDS board certified oral surgeon's new office - Harrowgate Dunmere Oral & Maxillofacial Surgery. See logo uploaded. See some images we would like included
Updates

Designs look the same

Font styles to use
Serif
Script

Colors
00AB8E
00BBA5
67D7C9
C6EFE9
E9F9F6

Requirements
Must have
• Color Pantone 623c. Also foldable business cards

```html
<!DOCTYPE html>
<html lang="en">
<head>
<meta charset="utf-8">
<title>Harrowgate Dunmere Oral &amp; Maxillofacial Surgery — Stationery</title>
<link rel="stylesheet" href="https://fonts.googleapis.com/css2?family=Arimo&family=Cormorant+Garamond:wght@500&family=Tinos:wght@400;700&display=swap">
<style>
:root{
  --bg:#d1d1d1;
  --paper:#ffffff;
  --sage:#b2c9bc;
  --sage-text:#9dbaa9;
  --ink:#3f3f3f;
  --rule:#555555;
  --muted:#666666;
}
*{margin:0;padding:0;box-sizing:border-box}
html,body{width:1200px;height:1055px;overflow:hidden;background:var(--bg)}
.canvas{position:relative;width:1200px;height:1055px}
.sheet{position:absolute;background:var(--paper);box-shadow:3px 4px 6px rgba(0,0,0,.28)}
.brand-name{font-family:"Cormorant Garamond",serif;font-weight:500;color:var(--sage-text);white-space:nowrap;text-align:center;position:absolute;left:0;right:0}
.band{position:absolute;left:0;right:0;height:7px;background:var(--sage)}
.band-tag{position:absolute;left:50%;transform:translateX(-50%);background:var(--paper);padding:0 4px;font-family:"Cormorant Garamond",serif;font-weight:500;color:var(--sage-text);white-space:nowrap}
.rule{position:absolute;left:0;right:0;height:2px;background:var(--rule)}
.icon{width:8px;height:8px;vertical-align:-1px;margin-right:6px}

/* letterhead */
.letterhead{left:53px;top:122px;width:573px;height:811px}
.lh-contact{position:absolute;left:38px;top:44px;font-family:Tinos,serif;font-size:9px;line-height:11.8px;color:var(--ink)}
.lh-address{position:absolute;right:38px;top:50px;text-align:right;font-family:Tinos,serif;font-size:9px;line-height:11.8px;color:var(--ink)}
.letterhead .brand-name{top:58px;font-size:21px}
.letterhead .band{top:95px}
.letterhead .band-tag{top:89px;font-size:11px;line-height:15px}
.letterhead .rule{top:107px}
.letter{position:absolute;left:52px;top:250px;width:480px;font-family:Arimo,sans-serif;color:var(--ink)}
.salutation{font-size:12px;margin-bottom:24px}
.letter p{font-size:9.2px;line-height:11.7px;margin-bottom:10.5px}
.signoff{position:absolute;left:52px;top:531px;font-family:Arimo,sans-serif;font-size:6.5px;color:var(--ink)}
.signature{position:absolute;left:56px;top:566px;width:82px;height:22px;background:#eeeeee;border-radius:2px}

/* business card front */
.card-front{left:662px;top:334px;width:485px;height:277px;background:var(--sage)}
.card-front .brand-name{top:97px;font-size:30px;color:#ffffff}
.card-front .tagline{position:absolute;left:0;right:0;top:141px;text-align:center;font-family:"Cormorant Garamond",serif;font-weight:500;font-size:17px;color:#ffffff}

/* business card back */
.card-back{left:662px;top:656px;width:485px;height:277px}
.card-back .brand-name{top:82px;font-size:21px}
.card-back .band{top:118px}
.card-back .band-tag{top:112px;font-size:12px;line-height:15px}
.card-back .rule{top:135px}
.person{position:absolute;right:255px;top:173px;text-align:right;font-family:Tinos,serif}
.person-name{font-weight:700;font-size:16px;color:var(--sage-text);letter-spacing:.3px}
.person-role{font-size:12px;color:var(--muted);margin-top:1px}
.divider{position:absolute;left:242px;top:169px;width:1px;height:43px;background:var(--rule)}
.card-contact{position:absolute;left:254px;top:166px;font-family:Tinos,serif;font-size:13px;line-height:17.6px;color:var(--muted)}
.card-contact .icon{width:10px;height:10px;margin-right:5px}
.card-address{position:absolute;left:0;right:0;top:241px;text-align:center;font-family:Tinos,serif;font-size:13px;color:var(--muted)}
</style>
</head>
<body>
<div class="canvas">

  <section class="sheet letterhead">
    <div class="lh-contact">
      <div><svg class="icon" viewBox="0 0 10 10"><path d="M2 1l2 2-1 1.3c.6 1.3 1.5 2.2 2.7 2.7L7 6l2 2-1.3 1.3C4.5 9 1 5.5.7 2.3z" fill="var(--sage)"/></svg>123-456-2100</div>
      <div><svg class="icon" viewBox="0 0 10 10"><rect x="0.5" y="2" width="9" height="6" fill="var(--sage)"/><path d="M.5 2l4.5 3.3L9.5 2" stroke="#fff" fill="none" stroke-width=".8"/></svg>youremail@gmail.com</div>
      <div><svg class="icon" viewBox="0 0 10 10"><circle cx="5" cy="5" r="4.3" fill="var(--sage)"/><path d="M.7 5h8.6M5 .7c-2.3 2.4-2.3 6.2 0 8.6M5 .7c2.3 2.4 2.3 6.2 0 8.6" stroke="#fff" fill="none" stroke-width=".6"/></svg>www.yourwebsite.com</div>
    </div>
    <div class="brand-name">Harrowgate Dunmere</div>
    <div class="lh-address">Your address<br>city<br>state, ZIP 0000</div>
    <div class="band"></div>
    <div class="band-tag">Oral &amp; Maxillofacial Surgery</div>
    <div class="rule"></div>

    <div class="letter">
      <div class="salutation">Dear Mr. Wrenfield,</div>
      <p>Lorem ipsum dolor sit amet, consectetuer adipiscing elit, sed diam nonmmy nibh euismod tincidunt ut laor eet dolore magna aliquam erat volutpat. Ut wisi enim ad minim veniam, quis nostrud exerci tationmcorper suscipit lobortis nisl ut aliquip ex ea commodo consequat. Duis autem vel eum iriure dolor in hendrerit in vulputate velit esse molestie consequat, vel illum dolore eu feugiat</p>
      <p>Rorem ipsum dolor sit amet, consectetuer adipiscing elit, sed diam nonmmy nibh euismod tincidunt ut laor eet dolore magna aliquam erat volutpat. Ut wisi enim ad minim veniam, quis nostrud exerci tationmcorper suscipit lobortis nisl ut aliquip ex ea commodo consequat. Duis autem vel eum iriure dolor in hendrerit in vulputate velit esse molest</p>
      <p>Dorem ipsum dolor sit amet, consectetuer adipiscing elit, sed diam nonmmy nibh euismod tincidunt ut laor eet dolore magna aliquam erat volutpat. Ut wisi enim ad minim veniam, quis nostrud exerci tationmcorper suscipit lobortis nisl ut aliquip ex ea commodo consequat. Duis autem vel eum iriure dolor in hendrerit in suscipit lobortis nisl ut aliquip ex ea commodo consequat. Duis autem vel eum iriure dolor in hendrerit in vulputate velit esse molestie consequat, vel illum</p>
      <p>Sorem ipsum dolor sit amet, consectetuer adipiscing elit, sed diam nonmmy nibh euismod tincidunt ut laor eet dolore magna aliquam erat volutpat. Ut wisi enim ad minim veniam, quis nostrud exerci tationmcorper suscipit lobortis nisl ut aliquip ex ea commodo consequat. Duis autem vel eum iriure dolor in</p>
    </div>
    <div class="signoff">Sincerely,</div>
    <div class="signature" role="img" aria-label="Handwritten signature of Elsabet Quorvane"></div>
  </section>

  <section class="sheet card-front">
    <div class="brand-name">Harrowgate Dunmere</div>
    <div class="tagline">Oral &amp; Maxillofacial Surgery</div>
  </section>

  <section class="sheet card-back">
    <div class="brand-name">Harrowgate Dunmere</div>
    <div class="band"></div>
    <div class="band-tag">Oral &amp; Maxillofacial Surgery</div>
    <div class="rule"></div>

    <div class="person">
      <div class="person-name">TOBIAS WRENFIELD</div>
      <div class="person-role">Manager</div>
    </div>
    <div class="divider"></div>
    <div class="card-contact">
      <div><svg class="icon" viewBox="0 0 10 10"><path d="M2 1l2 2-1 1.3c.6 1.3 1.5 2.2 2.7 2.7L7 6l2 2-1.3 1.3C4.5 9 1 5.5.7 2.3z" fill="none" stroke="var(--sage)" stroke-width=".9"/></svg>123-456-2100</div>
      <div><svg class="icon" viewBox="0 0 10 10"><rect x="0.7" y="2" width="8.6" height="6" fill="none" stroke="var(--sage)" stroke-width=".9"/><path d="M.7 2l4.3 3.3L9.3 2" stroke="var(--sage)" fill="none" stroke-width=".9"/></svg>youremail@gmail.com</div>
      <div><svg class="icon" viewBox="0 0 10 10"><circle cx="5" cy="5" r="4.3" fill="none" stroke="var(--sage)" stroke-width=".9"/><path d="M.7 5h8.6M5 .7c-2.3 2.4-2.3 6.2 0 8.6M5 .7c2.3 2.4 2.3 6.2 0 8.6" stroke="var(--sage)" fill="none" stroke-width=".7"/></svg>www.yourwebsite.com</div>
    </div>
    <div class="card-address">Your Address, City, State, Zip 0000</div>
  </section>

</div>
</body>
</html>
```